Italian restaurant needs new site

Need to make our website better.

Must have reservation module

Must be able to sell wine tasting tours and wine pairing tours and intégrate with dunmo desk

Blog

Social media

Wandervane ranking and last review.
Updates

Number of Pages Required

1 page

Font styles to use
Serif

Requirements
Must have
• Reservation module
• Marketplace to buy wine pairings and gift certificates
• Wandervane review
• Kindlepost posts
• All info from old site

```html
<!DOCTYPE html>
<html lang="en">
<head>
<meta charset="utf-8">
<title>Serata Bistro — Italian Cuisine &amp; Wine Bar</title>
<link href="https://fonts.googleapis.com/css2?family=Playfair+Display:ital,wght@0,400;0,700;1,400&family=PT+Serif:ital,wght@0,400;0,700;1,400&family=Fira+Sans:wght@400;500&display=swap" rel="stylesheet">
<style>
  :root{
    --ink-white:#ffffff;
    --wine:#8e1b24;
    --accent-red:#e0101f;
    --footer-bg:rgba(6,4,3,0.9);
    --widget-bg:#ffffff;
    --widget-ink:#222222;
    --widget-muted:#9a9a9a;
    --rating-bar:#6d6d6d;
    --rating-track:#dcdcdc;
    --kp-dark:#4a1518;
    --kp-red:#b3212c;
    --kp-grey:#e9ebee;
  }
  *{box-sizing:border-box;margin:0;padding:0}
  html,body{width:1200px;height:706px;overflow:hidden}
  body{position:relative;font-family:"Fira Sans",sans-serif;color:var(--ink-white);background:#140c06}
  .hero-bg{position:absolute;inset:0;
    background:
      radial-gradient(ellipse 220px 300px at 190px 340px, rgba(150,120,40,0.55), transparent 70%),
      radial-gradient(ellipse 260px 160px at 900px 560px, rgba(120,90,50,0.45), transparent 70%),
      radial-gradient(ellipse 200px 260px at 1020px 200px, rgba(110,80,30,0.35), transparent 70%),
      linear-gradient(180deg,#2a1a0c 0%,#1b1108 55%,#120b06 100%);}
  .social{position:absolute;left:13px;top:24px;display:flex;gap:10px;align-items:center}
  .social .dot{width:12px;height:12px;border-radius:50%;background:var(--ink-white)}
  .menu-toggle{position:absolute;left:1138px;top:12px;width:48px;height:41px;border:1px solid var(--ink-white);
    display:flex;flex-direction:column;justify-content:center;align-items:center;gap:6px}
  .menu-toggle span{display:block;width:28px;height:3px;background:var(--ink-white)}
  .brand{position:absolute;left:513px;top:0;width:173px;height:181px}
  .brand-name{position:absolute;left:0;top:0;width:173px;height:150px;display:flex;flex-direction:column;
    align-items:center;justify-content:center;gap:8px;font-family:"PT Serif",serif;font-size:22px;color:var(--wine);}
  .brand-name .mark{width:14px;height:14px;border-radius:50%;background:var(--wine)}
  .hero-title{position:absolute;left:0;top:252px;width:1200px;text-align:center;font-family:"Playfair Display",serif;
    font-size:56px;font-weight:400;line-height:1.1}
  .divider{position:absolute;left:505px;top:334px;width:190px;height:30px}
  .tagline{position:absolute;left:0;top:380px;width:1200px;text-align:center;font-family:"Playfair Display",serif;
    font-size:17px;letter-spacing:4px}
  .column{position:absolute;top:476px;width:239px}
  .column h2{display:flex;align-items:center;gap:9px;font-family:"Playfair Display",serif;font-weight:400;font-size:23px;height:28px}
  .col-blog{left:71px}.col-review{left:341px}.col-social{left:612px}.col-event{left:882px}
  .post-title{margin-top:18px;font-family:"PT Serif",serif;font-size:14px}
  .post-date{margin-top:10px;font-family:"PT Serif",serif;font-style:italic;font-size:10px}
  .post-text,.event-text{margin-top:6px;font-size:12px;line-height:19.5px}
  .event-text{margin-top:16px}
  .read-more{color:var(--accent-red);text-decoration:underline}
  .event-text .read-more{display:block;margin-top:9px;text-decoration:none;font-size:13px}
  .widget{margin-top:18px;width:239px;height:115px;background:var(--widget-bg);color:var(--widget-ink);overflow:hidden}
  .wv-head{height:45px;padding:4px 6px;border-bottom:1px solid #ccc}
  .wv-name{display:flex;align-items:center;gap:5px;font-family:"PT Serif",serif;font-size:15px}
  .wv-name .mark{width:10px;height:10px;border-radius:50%;background:var(--widget-ink)}
  .wv-sub{font-size:7px;color:var(--widget-muted);margin-top:6px}
  .wv-body{padding:10px 6px 0}
  .wv-link{font-size:11.5px;text-decoration:underline;font-weight:500}
  .wv-label{font-size:9px;font-weight:500;margin-top:10px}
  .wv-rating{margin-top:4px;width:56px;height:8px;border-radius:4px;background:var(--rating-track);overflow:hidden}
  .wv-rating span{display:block;width:90%;height:100%;background:var(--rating-bar)}
  .wv-note{font-size:8px;color:var(--widget-muted);margin-top:3px}
  .kp{background:var(--kp-grey);padding:2px}
  .kp-cover{position:relative;height:70px;background:linear-gradient(120deg,var(--kp-dark),var(--kp-red) 45%,#5a1a22 75%,#2a0c10);border:2px solid #222}
  .kp-avatar{position:absolute;left:3px;top:3px;width:28px;height:28px;background:#5b2a1e;border:1px solid #ddd}
  .kp-title{position:absolute;left:35px;top:2px;font-size:9.5px;color:#fff;font-weight:500}
  .kp-count{position:absolute;left:35px;top:14px;font-size:7px;color:#eee}
  .kp-like{position:absolute;left:4px;bottom:4px;background:#f5f6f7;color:#444;font-size:7px;padding:1px 5px;border:1px solid #ccc}
  .kp-name{position:absolute;right:6px;top:3px;font-size:7px;color:#eee}
  .kp-fans{margin-top:2px;background:#fff;height:41px;padding:3px 6px}
  .kp-fans p{font-size:7px;color:#555}
  .kp-faces{margin-top:3px;height:26px;background:linear-gradient(90deg,#b89a86,#8a6a5a,#c3a795,#7d5d4f,#b08f7e)}
  .site-footer{position:absolute;left:0;top:653px;width:1200px;height:53px;background:var(--footer-bg);
    display:flex;align-items:center;padding:0 14px;font-family:"PT Serif",serif;font-size:11.5px}
  .contact{display:flex;align-items:center;gap:6px;margin-right:18px}
  .contact svg{width:11px;height:11px;fill:var(--accent-red)}
  .copyright{margin-left:auto;margin-right:6px}
</style>
</head>
<body>
  <div class="hero-bg" role="img" aria-label="Dim, warm bokeh photo of a glass of white wine on a bistro table"></div>

  <nav class="social" aria-label="Social links">
    <span class="dot"></span><span class="dot"></span><span class="dot"></span><span class="dot"></span><span class="dot"></span>
    <svg width="14" height="11" viewBox="0 0 14 11" aria-label="Email"><rect x="0" y="0" width="14" height="11" rx="1" fill="#fff"/><path d="M0 1 L7 6 L14 1" stroke="#1b1108" stroke-width="1.4" fill="none"/></svg>
  </nav>

  <div class="menu-toggle" aria-label="Menu"><span></span><span></span><span></span></div>

  <header class="brand">
    <svg width="173" height="181" viewBox="0 0 173 181"><path d="M0 0 H173 V150 L86.5 181 L0 150 Z" fill="#fff"/></svg>
    <div class="brand-name"><span class="mark"></span>Serata Bistro</div>
  </header>

  <h1 class="hero-title">Welcome to the Serata Bistro</h1>
  <svg class="divider" viewBox="0 0 190 30" aria-hidden="true">
    <line x1="0" y1="20" x2="72" y2="20" stroke="#fff" stroke-width="1"/>
    <line x1="118" y1="20" x2="190" y2="20" stroke="#fff" stroke-width="1"/>
    <path d="M81 24 A14 14 0 0 1 109 24 Z" fill="#fff"/>
    <rect x="79" y="25" width="32" height="2.5" fill="#fff"/>
    <circle cx="95" cy="8" r="2" fill="#fff"/>
  </svg>
  <p class="tagline">ITALIAN CUISINE &amp; WINE BAR</p>

  <section class="column col-blog">
    <h2><svg width="22" height="18" viewBox="0 0 22 18"><path d="M2 15 A9 9 0 0 1 20 15 Z" fill="#fff"/><rect x="1" y="15.5" width="20" height="2" fill="#fff"/><circle cx="11" cy="4" r="1.5" fill="#fff"/></svg>Blog</h2>
    <p class="post-title">Lorem Ipsum is simply dummy text</p>
    <p class="post-date">13th June, 2017</p>
    <p class="post-text">Lorem Ipsum is simply dummy text of the printing and typesetting industry. Lorem Ipsum has been the. <span class="read-more">Read More</span></p>
  </section>

  <section class="column col-review">
    <h2><svg width="22" height="18" viewBox="0 0 22 18"><path d="M2 15 A9 9 0 0 1 20 15 Z" fill="#fff"/><rect x="1" y="15.5" width="20" height="2" fill="#fff"/><circle cx="11" cy="4" r="1.5" fill="#fff"/></svg>Review</h2>
    <div class="widget">
      <div class="wv-head">
        <div class="wv-name"><span class="mark"></span>Wandervane</div>
        <p class="wv-sub">Travel well. Dine well. Rest well.</p>
      </div>
      <div class="wv-body">
        <p class="wv-link">Serata Bistro</p>
        <p class="wv-label">Wandervane Traveler Rating</p>
        <div class="wv-rating" role="img" aria-label="Rating 4.5 out of 5"><span></span></div>
        <p class="wv-note">Based on 1,087 traveler reviews</p>
      </div>
    </div>
  </section>

  <section class="column col-social">
    <h2><svg width="22" height="18" viewBox="0 0 22 18"><path d="M2 15 A9 9 0 0 1 20 15 Z" fill="#fff"/><rect x="1" y="15.5" width="20" height="2" fill="#fff"/><circle cx="11" cy="4" r="1.5" fill="#fff"/></svg>Social Media</h2>
    <div class="widget kp">
      <div class="kp-cover" role="img" aria-label="Kindlepost page cover with abstract red artwork">
        <div class="kp-avatar"></div>
        <span class="kp-title">Serata Bistro</span>
        <span class="kp-count">3.469 Me gusta</span>
        <span class="kp-like">Te gusta</span>
        <span class="kp-name">Kindlepost</span>
      </div>
      <div class="kp-fans">
        <p>Te gusta esto</p>
        <div class="kp-faces" role="img" aria-label="Row of follower profile thumbnails"></div>
      </div>
    </div>
  </section>

  <section class="column col-event">
    <h2><svg width="22" height="18" viewBox="0 0 22 18"><path d="M2 15 A9 9 0 0 1 20 15 Z" fill="#fff"/><rect x="1" y="15.5" width="20" height="2" fill="#fff"/><circle cx="11" cy="4" r="1.5" fill="#fff"/></svg>Event</h2>
    <p class="event-text">Sell wine tasting tours and wine pairing tours and intégrate with dunmo desk <span class="read-more">Read More</span></p>
  </section>

  <footer class="site-footer">
    <span class="contact"><svg viewBox="0 0 12 12"><path d="M2.5 0.5 L4.5 0.5 L5.5 3.5 L4 4.8 A7 7 0 0 0 7.2 8 L8.5 6.5 L11.5 7.5 L11.5 9.5 A2 2 0 0 1 9.5 11.5 A9 9 0 0 1 0.5 2.5 A2 2 0 0 1 2.5 0.5 Z"/></svg>148 2290</span>
    <span class="contact"><svg viewBox="0 0 12 12"><path d="M6 0 A4.2 4.2 0 0 1 10.2 4.2 C10.2 7 6 12 6 12 C6 12 1.8 7 1.8 4.2 A4.2 4.2 0 0 1 6 0 Z M6 2.6 A1.6 1.6 0 1 0 6 5.8 A1.6 1.6 0 1 0 6 2.6 Z"/></svg>Calle Olivo 12, Centro, Bahía Serena, Mexico</span>
    <span class="contact"><svg viewBox="0 0 12 12"><path d="M6 0 A6 6 0 1 1 6 12 A6 6 0 1 1 6 0 Z M6 1.6 A4.4 4.4 0 1 0 6 10.4 A4.4 4.4 0 1 0 6 1.6 Z M5.3 3 H6.7 V5.7 L8.5 6.8 L7.8 7.9 L5.3 6.4 Z"/></svg>Open daily from 5 to 12 am</span>
    <span class="copyright">© 2017 Seratabistro.com. All rights reserved.</span>
  </footer>
</body>
</html>
```